Marketing Brochure: Category Management – Assortment Optimization

Create a compelling a 1-page marketing brochure around a service that allows Birch Continental retailers to optimize their product assortments in their stores. The brochure must be fun, very professionally done, clean, and exciting to want possible clients to want to pick up. See word file for content details. The Birch Worldwide Partners red and white colors should be used. Also, include relevant photos to liven up the brochure.

Target Market(s)

Birch Tools Retailers in Different Parts of the World

Industry/Entity Type

Retail

Font styles to use
Sans Serif

Requirements
Must have
• See Word file. Add some really good photos relevant to retail.
• Red and White Colors would be good to match Birch Worldwide Partners logo
• Also, should look like a 'global' service. Maybe add a worldly look to it.
Nice to have
• See World file
Should not have
• N/A

```html
<!DOCTYPE html>
<html lang="en">
<head>
<meta charset="utf-8">
<title>Category Management – Assortment Optimization</title>
<link href="https://fonts.googleapis.com/css2?family=Lato:wght@400;700;900&display=swap" rel="stylesheet">
<style>
:root{
  --red:#d0121b;
  --deep-red:#9e0f14;
  --ink:#333;
  --soft:#f1f1f1;
  --line:#e4e4e4;
  --bg:#dcdcdc;
  --white:#fff;
}
*{box-sizing:border-box;margin:0;padding:0}
html,body{width:960px;height:1200px;overflow:hidden}
body{background:var(--bg);font-family:'Lato',sans-serif;color:var(--ink);position:relative}
.page{position:absolute;top:289px;width:440px;height:622px;background:
  radial-gradient(circle at 20% 30%,rgba(0,0,0,.035) 0 120px,transparent 121px),
  radial-gradient(circle at 80% 10%,rgba(0,0,0,.03) 0 90px,transparent 91px),
  radial-gradient(circle at 70% 60%,rgba(0,0,0,.03) 0 140px,transparent 141px),
  var(--white);box-shadow:0 6px 18px rgba(0,0,0,.25);overflow:hidden}
.front{left:30px}
.back{left:490px}
.dot{position:absolute;border-radius:50%;background:var(--red)}
.dot.light{background:#f07a6a}
/* front */
.sphere-art{position:absolute;left:30px;top:40px;width:290px;height:290px;border-radius:50%;
  background:radial-gradient(circle at 40% 40%,#e9e9e9,#b9b9b9 55%,#8a1a1a 56%,#b8141a 70%,#ddd 71%,#c9c9c9)}
.globe-art{position:absolute;left:243px;top:268px;width:182px;height:182px;border-radius:50%;
  border:4px solid #9ea5ad;background:radial-gradient(circle at 45% 45%,#bfe3ff,#3f86c9 45%,#0c2a57 80%)}
.brand{position:absolute;left:21px;top:356px;width:205px;display:flex;align-items:center;gap:7px}
.brand-mark{flex:none;width:26px;height:26px;border-radius:50%;background:var(--red)}
.brand-name{font-weight:900;font-size:14px;line-height:15px;color:var(--deep-red)}
.front h1{position:absolute;left:21px;top:412px;font-size:17px;font-weight:900;line-height:21px;color:var(--red)}
.front h2{position:absolute;left:21px;top:463px;font-size:10.5px;font-weight:700;color:var(--deep-red)}
.front .copy{position:absolute;left:21px;right:21px;top:489px;font-size:7.4px;line-height:10.5px;text-align:justify}
.front .copy p+p{margin-top:8px}
.foot-band{position:absolute;left:0;right:0;bottom:0;height:22px;background:var(--red);color:var(--white);
  font-size:7.5px;text-align:center;line-height:22px}
/* back */
.section-tab{position:absolute;left:0;width:255px;height:26px;background:var(--red);
  border-radius:0 14px 14px 0;display:flex;align-items:center;color:var(--white);font-size:11px}
.section-tab::after{content:"";position:absolute;right:-6px;top:2px;width:255px;height:22px;border-right:2px solid var(--red);border-radius:0 12px 12px 0;pointer-events:none}
.tab-icon{width:40px;height:26px;background:var(--deep-red);display:flex;align-items:center;justify-content:center;margin-right:38px;
  clip-path:polygon(0 0,80% 0,100% 50%,80% 100%,0 100%)}
.tab-icon span{width:14px;height:14px;border:1.5px solid var(--white);border-radius:50%}
.ticks{position:absolute;left:28px;right:20px;list-style:none;font-size:7.6px;line-height:10px}
.ticks li{position:relative;padding-left:11px;margin-bottom:5px}
.ticks li::before{content:"";position:absolute;left:0;top:1px;width:3px;height:6px;border:solid var(--deep-red);border-width:0 1.5px 1.5px 0;transform:rotate(45deg)}
.service-tab{top:23px}.service-list{top:58px}
.roi-tab{top:158px}.roi-list{top:193px}
.work-art{position:absolute;left:0;right:0;top:310px;height:168px;
  background:linear-gradient(100deg,#c9d3dc,#eef1f4 45%,#b7c2cc)}
.about{position:absolute;left:26px;right:28px;top:495px}
.about h3{font-size:10.5px;font-weight:400;color:var(--red);text-decoration:underline;margin-bottom:6px}
.about p{font-size:7.4px;line-height:10.5px}
.rule{position:absolute;left:56px;right:0;height:2px;background:var(--red)}
.contact{position:absolute;left:26px;right:24px;top:598px;display:flex;justify-content:space-between;font-size:7.4px}
.contact span{display:flex;align-items:center;gap:5px}
.contact svg{width:9px;height:9px}
.back-band{position:absolute;left:0;right:0;bottom:0;height:5px;background:var(--red)}
.corner{position:absolute;right:-14px;top:-14px;width:36px;height:36px;border-radius:50%;background:var(--red)}
</style>
</head>
<body>

<section class="page front">
  <div class="dot" style="left:30px;top:38px;width:6px;height:6px"></div>
  <div class="dot" style="left:62px;top:18px;width:5px;height:5px"></div>
  <div class="dot" style="left:360px;top:55px;width:10px;height:10px"></div>
  <div class="dot light" style="left:415px;top:73px;width:9px;height:9px"></div>
  <div class="dot" style="left:370px;top:115px;width:24px;height:24px"></div>
  <div class="dot" style="left:368px;top:180px;width:10px;height:10px"></div>
  <div class="dot" style="left:60px;top:86px;width:8px;height:8px"></div>
  <div class="sphere-art" role="img" aria-label="Sphere wrapped in red ribbons showing retail and teamwork photos"></div>
  <div class="globe-art" role="img" aria-label="Glowing blue world map globe"></div>
  <div class="brand"><span class="brand-mark"></span><span class="brand-name">BIRCH WORLDWIDE<br>PARTNERS</span></div>
  <h1>Category Management –<br>Assortment Optimization</h1>
  <h2>Satisfying Customers with Data-Driven, Informed Decisions</h2>
  <div class="copy">
    <p>It takes a strong category strategy to drive sales growth. With changes in consumer demands and product introductions constantly making their way into the market, it's not easy to optimize product selection toward maximizing market share and wider profit margins. To do so, companies need to quickly and effectively deploy well-established and nimble methodologies that refine and enhance category assortment and retail space decisions.</p>
    <p>Birch Worldwide Partners category management's monthly services provides your business industry expertise, functional richness, and retail data analytics know-how to drive more profitable and productive product assortments. We speak analytics. In doing so, we synthesize raw data, assess it, and covert it into practical, measured solutions to help your business grow.</p>
  </div>
  <div class="foot-band">www.birchworldwidepartners.com</div>
</section>

<section class="page back">
  <div class="corner"></div>
  <div class="dot" style="left:378px;top:24px;width:14px;height:14px"></div>
  <div class="dot" style="left:402px;top:38px;width:8px;height:8px"></div>
  <div class="dot light" style="left:408px;top:88px;width:14px;height:14px"></div>
  <div class="dot" style="left:350px;top:97px;width:6px;height:6px"></div>
  <div class="dot" style="left:382px;top:105px;width:5px;height:5px"></div>
  <div class="dot" style="left:356px;top:136px;width:12px;height:12px"></div>
  <div class="dot" style="left:328px;top:153px;width:5px;height:5px"></div>
  <div class="dot" style="left:393px;top:130px;width:5px;height:5px"></div>

  <div class="section-tab service-tab"><div class="tab-icon"><span></span></div>Our Service Approach:</div>
  <ul class="ticks service-list">
    <li>Understand your long-term vision, market and assortment objectives</li>
    <li>Assess the current state of affairs to your categories</li>
    <li>Obtain store level raw data one category at a time</li>
    <li>Covert raw data into powerful insights about category performance,<br>opportunities, potential impact, and goal setting</li>
    <li>Implement recommendations, track results, and further advise</li>
  </ul>

  <div class="section-tab roi-tab"><div class="tab-icon"><span></span></div>Return on Investment:</div>
  <ul class="ticks roi-list">
    <li>Increased profitability and turnover</li>
    <li>Simplify assortments and planograms create a more consumer-friendly shopping experience</li>
    <li>Attack over-SKU'd categories and less duplication</li>
    <li>Fact-based analytics with collaborative market insights</li>
    <li>Reduce wasteful spending and to help brands help retailers compete more effectively</li>
    <li>Acquired processes are safeguarded for the long-term</li>
    <li>The customer remains at the heart of decision making</li>
  </ul>

  <div class="work-art" role="img" aria-label="Hands working with a tablet over a network of analytics icons"></div>

  <div class="about">
    <h3>About Birch Worldwide Partners:</h3>
    <p>Birch Worldwide Partners is an Birch Tools International consulting service that provides training and strategy recommendations based on Birch's 94-year retail industry expertise. Our services drive significant and sustainable performance improvements so you can accomplish your company's most important business objectives</p>
  </div>
  <div class="rule" style="top:570px"></div>
  <div class="rule" style="top:576px;left:240px;height:1px"></div>

  <div class="contact">
    <span><svg viewBox="0 0 10 10"><path d="M2 1l2 2-1 1.5c.6 1.2 1.3 1.9 2.5 2.5L7 6l2 2-1.3 1.3C4.5 9 1 5.5.7 2.3z" fill="#333"/></svg>555.210.4380</span>
    <span><svg viewBox="0 0 10 10"><rect x=".5" y="2" width="9" height="6" fill="none" stroke="#333"/><path d="M.5 2l4.5 3.5L9.5 2" fill="none" stroke="#333"/></svg>jmorales@birchtools.com</span>
    <span><svg viewBox="0 0 10 10"><circle cx="5" cy="5" r="4.3" fill="none" stroke="#333"/><path d="M.7 5h8.6M5 .7c-2.4 2.6-2.4 6 0 8.6M5 .7c2.4 2.6 2.4 6 0 8.6" fill="none" stroke="#333" stroke-width=".8"/></svg>www.birchworldwidepartners.com</span>
  </div>
  <div class="back-band"></div>
</section>

</body>
</html>
```